Dalvick's Business Card

I need some designs for a new business card including the new logo attached. An old example of our business card is also attached to show all the data that should be included on the new design.
**I added some more examples someone had mocked up**

Contact Information for Business Card

Should include all info on other examples uploaded.

```html
<!DOCTYPE html>
<html lang="en">
<head>
<meta charset="utf-8">
<title>Dalvick's Business Card</title>
<link href="https://fonts.googleapis.com/css2?family=Barlow+Condensed:wght@400;500;600;700&display=swap" rel="stylesheet">
<style>
  :root {
    --brand-blue: #0b6fb5;
    --brand-red: #e31e25;
    --card-white: #f4f4f4;
    --backdrop: #e4e4e4;
  }
  * { margin: 0; padding: 0; box-sizing: border-box; }
  html, body {
    width: 1200px; height: 960px; overflow: hidden;
    background: var(--backdrop);
    font-family: "Barlow Condensed", "Arial Narrow", sans-serif;
  }
  .card {
    position: absolute; left: 295px; width: 610px; height: 348px; overflow: hidden;
  }
  .card-front { top: 109px; }
  .card-back { top: 511px; background: var(--card-white); }
  .card-shapes { position: absolute; inset: 0; width: 610px; height: 348px; }
  .front-text { position: absolute; color: #fff; font-weight: 600; white-space: nowrap; line-height: 1; }
  .service-area { top: 26px; left: 0; width: 100%; text-align: center; font-size: 21px; }
  .call-to-action { top: 301px; left: 0; width: 100%; text-align: center; font-size: 22px; }
  .ribbon-label { position: absolute; font-weight: 700; font-size: 19px; line-height: 1; white-space: nowrap; }
  .ribbon-licensed { left: 53px; top: 155px; color: var(--brand-blue); transform: rotate(4deg); transform-origin: left top; }
  .ribbon-family { left: 398px; top: 178px; color: var(--brand-red); transform: rotate(-11deg); }
  .brand-mark {
    position: absolute; display: flex; align-items: center; gap: 8px;
    color: var(--brand-blue); font-weight: 700; white-space: nowrap; line-height: 1;
  }
  .brand-mark .brand-dot { border-radius: 50%; background: var(--brand-red); }
  .front-brand { left: 232px; top: 175px; font-size: 34px; }
  .front-brand .brand-dot { width: 16px; height: 16px; }
  .back-brand { left: 45px; top: 150px; font-size: 44px; }
  .back-brand .brand-dot { width: 22px; height: 22px; }
  .person { position: absolute; right: 48px; top: 70px; text-align: right; color: #fff; }
  .person-name { font-size: 23px; font-weight: 700; line-height: 1.1; }
  .person-role { font-size: 15px; font-weight: 400; }
  .contact-list { position: absolute; right: 48px; top: 238px; list-style: none; color: #fff; font-size: 15px; }
  .contact-list li { display: flex; justify-content: flex-end; align-items: center; gap: 7px; height: 21px; }
  .contact-list svg { width: 13px; height: 13px; }
</style>
</head>
<body>

<section class="card card-front" aria-label="Card front">
  <svg class="card-shapes" viewBox="0 0 610 348" aria-hidden="true">
    <rect width="610" height="348" fill="var(--brand-blue)"/>
    <path d="M0 144 C120 146 220 162 330 164 C440 164 530 146 610 124 V348 H0 Z" fill="var(--card-white)"/>
    <path d="M0 216 C90 198 200 202 300 218 C400 232 520 214 610 191 V348 H0 Z" fill="var(--brand-red)"/>
  </svg>
  <p class="front-text service-area">Serves Maple Falls, IA &amp; Surrounding Areas</p>
  <p class="ribbon-label ribbon-licensed">LICENSED &amp; INSURED</p>
  <div class="brand-mark front-brand"><span class="brand-dot"></span>Dalvick's</div>
  <p class="ribbon-label ribbon-family">FAMILY OWNED &amp; OPERATED</p>
  <p class="front-text call-to-action">Call Today For All Your Hvac, Refrigeration &amp; Plumbing Needs</p>
</section>

<section class="card card-back" aria-label="Card back">
  <svg class="card-shapes" viewBox="0 0 610 348" aria-hidden="true">
    <path d="M265 0 H610 V172 H388 Q365 172 352 150 Z" fill="var(--brand-blue)"/>
    <path d="M388 177 H610 V348 H267 L352 199 Q365 177 388 177 Z" fill="var(--brand-red)"/>
  </svg>
  <div class="brand-mark back-brand"><span class="brand-dot"></span>Dalvick's</div>
  <div class="person">
    <p class="person-name">Marcus Dalvick</p>
    <p class="person-role">Co-Owner</p>
  </div>
  <ul class="contact-list">
    <li>555.014.2287
      <svg viewBox="0 0 24 24" aria-hidden="true"><path d="M6.6 10.8a15 15 0 0 0 6.6 6.6l2.2-2.2a1 1 0 0 1 1-.25 11 11 0 0 0 3.6.6 1 1 0 0 1 1 1V20a1 1 0 0 1-1 1A17 17 0 0 1 3 4a1 1 0 0 1 1-1h3.5a1 1 0 0 1 1 1 11 11 0 0 0 .6 3.6 1 1 0 0 1-.25 1Z" fill="#fff"/></svg>
    </li>
    <li>service@dalvickhvac.net
      <svg viewBox="0 0 24 24" aria-hidden="true"><rect x="2" y="5" width="20" height="14" rx="1" fill="none" stroke="#fff" stroke-width="2.4"/><path d="M3 6 L12 13 L21 6" fill="none" stroke="#fff" stroke-width="2.4"/></svg>
    </li>
  </ul>
</section>

</body>
</html>
```